The most modern business card ever !!!

Our company call “Vendalo”. Vendalo is a technology company specialized in cruises solutions. Out main product is a platform to reserve cruises. This is a revolutionary platform that make easier to travel agencies and final users to reserve cruises across dozen companies like tibba, wernu, hpv, dgb, etc..We are a “start up”, with a young team of developers and we want to transmit it.. For it, we want something different, a modern business card that represent cruises and technology.. When someone receive this card, this person should say: wowww this is different… this is modern… this is a cruise related company..
- diferent, modern
- traditions business card

```html
<!DOCTYPE html>
<html lang="en">
<head>
<meta charset="utf-8">
<title>Vendalo Business Card</title>
<link rel="stylesheet" href="https://fonts.googleapis.com/css2?family=Questrial&display=swap">
<style>
  :root {
    --page: #ffffff;
    --frame: #000000;
    --card-grey: #808080;
    --ink: #1b1b1b;
    --accent: #29a8e0;
    --hull-light: #f4f4f4;
    --hull-shade: #bdbdbd;
  }
  html, body {
    margin: 0;
    padding: 0;
    width: 1200px;
    height: 686px;
    overflow: hidden;
    background: var(--page);
  }
  .card {
    position: relative;
    width: 1200px;
    height: 686px;
    box-sizing: border-box;
    background: var(--frame);
    border-bottom-left-radius: 380px 360px;
    padding: 11px;
  }
  .card-face {
    position: relative;
    width: 100%;
    height: 100%;
    background: var(--card-grey);
    border-bottom-left-radius: 360px 340px;
    overflow: hidden;
  }
  .emblem-drop {
    position: absolute;
    left: 64px;
    top: 53px;
    width: 542px;
    height: 565px;
    background: var(--frame);
    border-radius: 0 50% 50% 50%;
  }
  .ship-illustration {
    position: absolute;
    left: 52px;
    top: 130px;
    width: 450px;
    height: 290px;
    border-radius: 60px 40px 120px 40px;
    background: linear-gradient(160deg, var(--hull-light) 0%, var(--hull-shade) 100%);
  }
  .brand {
    position: absolute;
    left: 724px;
    top: 236px;
    font-family: "Questrial", "Helvetica Neue", Arial, sans-serif;
    color: var(--ink);
  }
  .brand-row {
    display: flex;
    align-items: center;
    gap: 12px;
    margin-left: -24px;
  }
  .brand-mark {
    width: 12px;
    height: 12px;
    background: var(--accent);
    flex: none;
  }
  .brand-name {
    margin: 0;
    font-size: 88px;
    line-height: 1;
    font-weight: 400;
    letter-spacing: 1px;
  }
  .brand-slogan {
    margin: 4px 0 0 2px;
    font-size: 36px;
    line-height: 1;
    font-variant: small-caps;
    letter-spacing: 3px;
  }
</style>
</head>
<body>
  <div class="card">
    <div class="card-face">
      <div class="emblem-drop">
        <div class="ship-illustration" role="img" aria-label="Illustration of a white cruise ship bow sailing forward"></div>
      </div>
      <div class="brand">
        <div class="brand-row">
          <span class="brand-mark"></span>
          <h1 class="brand-name">Vendalo</h1>
        </div>
        <p class="brand-slogan">Your Slogan Here</p>
      </div>
    </div>
  </div>
</body>
</html>
```